Velvet Ladle Wishes Website Design; Cupcake Business with a unique and bespoke design element

We need a website design for a new bespoke and unique business making gourmet cupcakes - but MOST IMPORTANTLY we design and handmake cupcake wrappers and toppers specifically for each client's event. We are based in Sydney, Australia. The final resulting website should be elegant yet whimsical reflecting the notion of dreams and very elegant events eg weddings and very special parties.

We want to eventually have about 5 pages, HOWEVER, this project is specifically for the first page (ie Home page) and one other only. The final required pages are: a HOME page; ABOUT US page; PHOTO GALLERY page; FLAVOUR MENU & OTHER PRODUCTS page; CONTACT & INTERNET ENQUIRY page.

We expect the HOME page to be quite elaborate, perhaps including some animation. We will be providing the text content for all the other pages, and basically they will have the same background as the home page. We are looking for a clean design that runs across each page thus giving the website a continuity that pulls it all together. We would like our logo to be included on each page.

PLEASE NOTE: We will want multiple pages worked on in the handover phase but initially we want a very concise, consistent template to limit the amount of work to prospective designers.

While we are primarily looking for the design phase to be covered by this project, we would certainly appreciate coding to be included and will take that into consideration when choosing a winner.
Updates

Hi Designers

We have added some more information to our brief - please review it.

Thanks and happy designing

Hi Designers

Please note that we have increased our Prize money to $750.00.  We hope this encourages you to participate.

Thanks and regards
Velvet Ladle Wishes

Hi Designers

We've just posted some photos to help give you an idea of what we do.  Please note our attention to detail and precision in our work.

Thanks
Velvet Ladle Wishes

Hi Designers

Please Note:  What makes us different  to any other cupcake business is that we design cupcake wrappers and toppers, unique to our client's event whether it be a wedding, a birthday party or product launch.  We consult with our client to understand themes, colours, styles etc.  We then have our designs printed, next they are cut by a specialised computerised cutting machine,  We assemble everything by hand, and usually embellish the wrapper and topper with pearls, crystals, feathers, lace, ribbons or whatever else is appropriate for the event.  All work is totally bespoke, unique and individual.  No other cupcake supplier that we know of goes to these lengths to satisfy their client's dreams.

THE WRAPPER AND TOPPER IS OUR PRIMARY SELLING POINT. 

PLEASE NOTE:- We have uploaded a new photograph which we want to be used as the main photograph on the landing page.

We have removed all previous photographs of cupcakes (except for one that we can't get rid of).

We don't want a picture of a cupcake on the landing page we want the image _D7C3239.jpg to be used for that purpose.

We have also uploaded our logo in a number of file formats as we have had requests from you for these.

Hi designers

we have a crazy busy weekend on and won't be able to make any decisions re our competition until Monday  -  sorry to keep you in suspense, just a couple more days please!

regards
Pam

Target Market(s)

Primarily women - brides, new mothers (Christenings), Event Planners, who place an emphasis on the beauty of a product rather than the cost

Industry/Entity Type

Events

Requirements
Must have
• It must have our Logo (see attached upload) on each page (our logo is a butterfly atop a cupcake resting on a spoon and our motto is "Creating Delicious Works of Art". The colours used are pale pink, blue and chocolate brown and we'd expect these colours to be repeated in the final website.
The website must have a photo gallery which we can access and add to/change as our business grows.
We need a contact page which has an "internet enquiry form".
There should be a "Menu" page describing our cupcake flavours.
The Home page must have a party/event feel to it - definitely making an enquirer want to enter further into the site.
Nice to have
• Our logo is attached below in the "uploads". One idea that we have had is to use the butterfly in the logo but start it as a caterpillar crawling on the screen; as it spins it's cocoon the words "Sweet Dreams Little Caterpillar" would appear on screen; this would incorporate the "Dreams" in our Business Name; then our logo butterfly would hatch. This encapsulates the idea of taking something plain (caterpillar/cupcake) and creating something beautiful (butterfly/OUR cupcake).
However, we are open to other design ideas.
The colours we would like to have are pale pink, blue and chocolate brown in the design.

Some websites we really admire are: www.mirabellhart.com www.ribbonglitterloaf.com.au and www.greetingsoriel.com.au
These websites have a lightness and sense of fantasy to them. They do not convey a corporate image at all, rather they make you want to be at the party.
Should not have
• No "Corporate" style.

Most Important: We already have a website which we are not happy with - that is why we are going through this exercise to replace it. That means we DO NOT want anything along the lines of our current website. We are expecting some fresh ideas for our prize money.

```html
<!DOCTYPE html>
<html lang="en">
<head>
<meta charset="utf-8">
<title>Velvet Ladle Wishes – About Us</title>
<link href="https://fonts.googleapis.com/css2?family=Alex+Brush&family=Arimo:wght@400;700&family=Libre+Baskerville&display=swap" rel="stylesheet">
<style>
  :root {
    --navy: #022d5c;
    --pink: #f26aaa;
    --heading-pink: #ee5da6;
    --ink: #0c2a52;
    --panel: #fdfcfd;
    --nav-bar: #e9e8e9;
    --white: #ffffff;
    --bg-light: #f3f1ef;
    --bg-mid: #c9c3bb;
    --bg-dark: #7d776f;
  }
  * { margin: 0; padding: 0; box-sizing: border-box; }
  html, body { width: 1200px; height: 779px; overflow: hidden; background: var(--white); }
  .page { position: relative; width: 1200px; height: 779px; overflow: hidden; font-family: "Arimo", Arial, sans-serif; }

  .top-band { position: absolute; left: 0; top: 17px; width: 1200px; height: 15px; background: var(--navy); }
  .top-rule { position: absolute; left: 0; top: 32px; width: 1200px; height: 3px; background: var(--pink); }

  .hero-backdrop {
    position: absolute; left: 0; top: 35px; width: 1200px; height: 666px;
    background:
      linear-gradient(180deg, rgba(255,255,255,0.95) 0%, rgba(255,255,255,0) 14%, rgba(255,255,255,0) 86%, rgba(255,255,255,0.95) 100%),
      linear-gradient(90deg, var(--bg-dark) 0%, var(--bg-mid) 6%, var(--bg-light) 12%, var(--bg-light) 88%, var(--bg-mid) 94%, var(--bg-dark) 100%);
  }

  .panel { position: absolute; left: 105px; top: 98px; width: 990px; height: 549px; border-radius: 8px; background: var(--panel); box-shadow: 0 1px 6px rgba(0,0,0,0.18); overflow: hidden; }
  .nav-bar { position: absolute; left: 0; top: 0; width: 990px; height: 58px; background: var(--nav-bar); border-bottom: 5px solid #b8b6b5; }

  .nav-tab-active { position: absolute; left: 187px; top: 92px; width: 111px; height: 59px; background: var(--navy); border-radius: 2px 2px 0 0; }
  .main-nav { position: absolute; left: 0; top: 0; font-family: "Libre Baskerville", Georgia, serif; font-size: 21px; color: var(--ink); }
  .main-nav span { position: absolute; top: 116px; white-space: nowrap; }
  .main-nav .is-current { color: var(--white); }

  .social-button { position: absolute; top: 107px; width: 34px; height: 34px; border-radius: 5px; background: #f4f4f4; box-shadow: 0 1px 3px rgba(0,0,0,0.25); }

  .brand { position: absolute; left: 139px; top: 380px; width: 263px; text-align: center; }
  .brand-dot { display: block; width: 46px; height: 46px; margin: 0 auto 12px; border-radius: 50%; background: var(--pink); }
  .brand-name { font-size: 24px; color: var(--navy); font-weight: 400; }

  .section-title { position: absolute; left: 481px; top: 196px; font-family: "Alex Brush", cursive; font-size: 46px; font-weight: 400; color: var(--heading-pink); }
  .about-copy { position: absolute; left: 485px; top: 260px; width: 540px; font-size: 15.4px; line-height: 20.4px; letter-spacing: 0.06em; color: var(--ink); }
  .about-copy p { margin-bottom: 20px; }

  .page-links { position: absolute; left: 487px; top: 590px; font-size: 15.4px; letter-spacing: 0.06em; color: var(--pink); }

  .bottom-rule { position: absolute; left: 0; top: 701px; width: 1200px; height: 4px; background: var(--pink); }
  .footer { position: absolute; left: 0; top: 705px; width: 1200px; height: 74px; background: var(--navy); color: var(--white); font-weight: 700; }
  .copyright { position: absolute; left: 0; width: 1200px; top: 34px; text-align: center; font-size: 11px; }
  .sound-icon { position: absolute; left: 964px; top: 19px; }
  .sound-toggle { position: absolute; left: 1016px; top: 38px; font-size: 13.5px; }
</style>
</head>
<body>
<div class="page">
  <div class="top-band"></div>
  <div class="top-rule"></div>

  <div class="hero-backdrop" role="img" aria-label="Soft photograph of handmade cupcake wrappers and toppers with lace, pearls and paper roses"></div>

  <div class="panel">
    <div class="nav-bar"></div>
  </div>

  <div class="nav-tab-active"></div>
  <nav class="main-nav">
    <span class="is-current" style="left:215px">Home</span>
    <span style="left:322px">About Us</span>
    <span style="left:449px">Gallery</span>
    <span style="left:569px">Flavour Menu</span>
    <span style="left:743px">Contact Us</span>
  </nav>

  <div class="social-button" style="left:899px" aria-label="Social link"></div>
  <div class="social-button" style="left:950px" aria-label="Social link"></div>
  <div class="social-button" style="left:1004px" aria-label="Social link"></div>

  <div class="brand">
    <span class="brand-dot"></span>
    <div class="brand-name">Velvet Ladle Wishes</div>
  </div>

  <h1 class="section-title">About Us</h1>
  <div class="about-copy">
    <p>Aliquam congue fermentum nisl. Mauris accumsan nulla vel diam.<br>Sed in lacus ut enim adipiscing aliquet.</p>
    <p>Nulla venenatis. In pede mi, aliquet sit amet, euismod in, auctor<br>ut, ligula. Aliquam dapibus tincidunt metus. Praesent justo dolor,<br>lobortis quis, lobortis dignissim, pulvinar ac, lorem. Vestibulum<br>sed ante. Donec sagittis euismod purus.</p>
    <p>Aliquam congue fermentum nisl. Mauris accumsan nulla vel diam.<br>Sed in lacus ut enim adipiscing aliquet.</p>
    <p>Nulla venenatis. In pede mi, aliquet sit amet, euismod in, auctor<br>ut, ligula. Aliquam dapibus tincidunt metus. Praesent justo dolor,<br>lobortis quis, lobortis dignissim, pulvinar ac, lorem. Vestibulum<br>sed ante. Donec sagittis euismod purus.</p>
  </div>
  <div class="page-links">Home&nbsp; |&nbsp;&nbsp; Gallery</div>

  <div class="bottom-rule"></div>
  <footer class="footer">
    <div class="copyright">© Copyright 2012&nbsp; |&nbsp; Velvet Ladle Wishes&nbsp; |&nbsp; All Rights Reserved</div>
    <svg class="sound-icon" width="40" height="33" viewBox="0 0 40 33" aria-label="Sound level">
      <rect x="0" y="19" width="6" height="14" fill="#ffffff"/>
      <rect x="8" y="13" width="6" height="20" fill="#ffffff"/>
      <rect x="16" y="6" width="6" height="27" fill="#ffffff"/>
      <rect x="24" y="0" width="6" height="33" fill="#ffffff"/>
      <rect x="32" y="8" width="6" height="25" fill="#ffffff"/>
    </svg>
    <div class="sound-toggle">OFF&nbsp; |&nbsp; ON</div>
  </footer>
</div>
</body>
</html>
```